Fern Acupuncture Business Card Design

I would like a business card design for my acupuncture business which is based from 2 practices in Melbourne, Australia.

The front of the card should include:

*The Logo
* Name - Miranda Tesselhoff (B.App.Sc.(TCM), Dip.Rem.Mass.). (I would like the letters after my name in slightly smaller font)
* Mobile number - 0472 318 604
* Web address - www.fernacupuncture.com.au

On the back of the card I would somehow like to fit my 2 clinic addresses in. They are:

The Calm & Balance Rooms
842 Pellam St, Camberwell VIC 3124
Ph: 1300 287 419

Riverbend Natural Therapies & Herbal Practice
19 Quillon Ave, Malvern East VIC 3145
Ph: (03) 9731 4052

If there is space, I'd also like to add to the back of the card - Next Appointment............................ (or something along those lines).

Thanks and happy designing!

Target Market(s)

Health consumers, and colleagues in the health industry

Industry/Entity Type

Clinic

Contact Information for Business Card

as above in brief

Requirements
Must have
• I've seen some ok designs coming in, however I'd like to avoid the generic look with the added curved line details etc. I don't particularly need extra patterns added to the card. I'd prefer it to look quite clean and simple, and using more earthy colours (I'm not super keen on the lime green that a lot of designs seem to include. I don't mind the full black or white look, (obviously the back side needs to be a lighter colour to allow me to write appointment details on it). I also quite like the idea of the background looking like brown recycled paper (just an idea - that's not 100% necessary).
Nice to have
• I have an idea that I could have the main flower part of the logo printed as metallic.
Should not have
• Generic patterns and too much added detail.

```html
<!DOCTYPE html>
<html lang="en">
<head>
<meta charset="utf-8">
<title>Fern Acupuncture – Business Card</title>
<link href="https://fonts.googleapis.com/css2?family=Arimo:wght@400;700&display=swap" rel="stylesheet">
<style>
  :root {
    --backdrop: #6f7278;
    --card-white: #ffffff;
    --ink: #111111;
    --ink-soft: #333333;
    --rule: #1a1a1a;
    --band: #0c0c0c;
    --accent: #c9a46a;
    --band-text: #e6e1d8;
    --divider: #5a5550;
    --tint-a: rgba(190, 160, 115, 0.28);
    --tint-b: rgba(190, 160, 115, 0);
  }
  * { box-sizing: border-box; margin: 0; padding: 0; }
  html, body { width: 1200px; height: 960px; overflow: hidden; }
  body {
    background: var(--backdrop);
    font-family: "Arimo", Arial, sans-serif;
    color: var(--ink);
    display: flex;
    flex-direction: column;
    align-items: center;
    justify-content: center;
    gap: 60px;
  }
  .card {
    position: relative;
    width: 640px;
    height: 390px;
    background: var(--card-white);
    border-radius: 10px 70px 10px 70px;
    overflow: hidden;
    box-shadow: 0 6px 18px rgba(0,0,0,0.25);
  }

  /* Front */
  .front-tint {
    position: absolute;
    right: 0; top: 0;
    width: 380px; height: 390px;
    background: radial-gradient(ellipse 80% 70% at 85% 45%, var(--tint-a), var(--tint-b) 75%);
  }
  .brand {
    position: absolute;
    left: 40px; top: 92px;
    display: flex; align-items: center; gap: 14px;
  }
  .brand-mark {
    width: 120px; height: 120px;
    border-radius: 50%;
    background: var(--ink);
  }
  .brand-name {
    font-size: 17px; font-weight: 700; color: var(--ink);
    width: 110px; line-height: 1.25;
  }
  .identity {
    position: absolute;
    right: 40px; top: 58px;
    text-align: right;
  }
  .identity-name { font-size: 26px; font-weight: 700; }
  .identity-credentials { font-size: 11px; font-weight: 700; margin-top: 4px; }
  .identity-rule {
    position: absolute; right: 40px; top: 118px;
    width: 280px; border-top: 1px solid var(--rule);
  }
  .contact-rule {
    position: absolute; left: 40px; bottom: 110px;
    width: 400px; border-top: 1px solid var(--rule);
  }
  .contact-list {
    position: absolute; left: 40px; bottom: 34px;
    list-style: none;
  }
  .contact-list li {
    display: flex; align-items: center; gap: 22px;
    font-size: 17px; font-weight: 700; color: var(--ink-soft);
    margin-top: 12px;
  }
  .contact-list svg { width: 16px; height: 16px; flex: none; }

  /* Back */
  .appointment {
    position: absolute; left: 0; top: 0;
    width: 100%; height: 215px;
  }
  .appt-line {
    position: absolute; border-top: 1px solid var(--rule);
  }
  .appt-label {
    position: absolute; left: 0; right: 0; top: 98px;
    text-align: center; font-size: 18px; font-weight: 700;
  }
  .clinic-band {
    position: absolute; left: 0; bottom: 0;
    width: 100%; height: 175px;
    background: var(--band);
    display: flex; align-items: center;
    padding: 0 34px;
  }
  .clinic {
    flex: 1;
    color: var(--band-text);
    font-size: 14px; line-height: 1.45;
  }
  .clinic + .clinic {
    border-left: 1px solid var(--divider);
    padding-left: 26px;
  }
  .clinic-name {
    color: var(--accent); font-weight: 700; font-size: 17px;
    line-height: 1.2; margin-bottom: 8px; width: 250px;
  }
  .clinic-phone { display: flex; align-items: center; gap: 8px; }
  .clinic-phone svg { width: 12px; height: 12px; fill: var(--accent); }
</style>
</head>
<body>

<section class="card card-front" aria-label="Card front">
  <div class="front-tint" role="img" aria-label="Soft warm paper-toned tint"></div>
  <div class="brand">
    <div class="brand-mark"></div>
    <div class="brand-name">Fern Acupuncture</div>
  </div>
  <div class="identity">
    <div class="identity-name">Miranda Tesselhoff</div>
    <div class="identity-credentials">(B.App.Sc.(TCM), Dip.Rem.Mass.)</div>
  </div>
  <div class="identity-rule"></div>
  <div class="contact-rule"></div>
  <ul class="contact-list">
    <li>
      <svg viewBox="0 0 16 16" aria-hidden="true"><rect x="4" y="1" width="8" height="14" rx="1.5" fill="none" stroke="#111" stroke-width="1.5"/><line x1="7" y1="12.5" x2="9" y2="12.5" stroke="#111" stroke-width="1.2"/></svg>
      0472 318 604
    </li>
    <li>
      <svg viewBox="0 0 16 16" aria-hidden="true"><circle cx="8" cy="8" r="7" fill="none" stroke="#111" stroke-width="1.4"/><ellipse cx="8" cy="8" rx="3" ry="7" fill="none" stroke="#111" stroke-width="1.1"/><line x1="1" y1="8" x2="15" y2="8" stroke="#111" stroke-width="1.1"/></svg>
      www.fernacupuncture.com.au
    </li>
  </ul>
</section>

<section class="card card-back" aria-label="Card back">
  <div class="appointment">
    <div class="appt-line" style="left:170px; right:40px; top:34px;"></div>
    <div class="appt-line" style="left:210px; right:40px; top:64px;"></div>
    <div class="appt-label">Next Appointment</div>
    <div class="appt-line" style="left:40px; right:210px; top:150px;"></div>
    <div class="appt-line" style="left:40px; right:170px; top:180px;"></div>
  </div>
  <div class="clinic-band">
    <div class="clinic">
      <div class="clinic-name">The Calm &amp; Balance Rooms</div>
      <div>842 Pellam St, Camberwell VIC 3124</div>
      <div class="clinic-phone">
        <svg viewBox="0 0 12 12" aria-hidden="true"><path d="M2.5 1 L4.5 1 L5 3.5 L3.8 4.4 Q5 7 7.6 8.2 L8.5 7 L11 7.5 L11 9.5 Q10.5 11 9 11 Q1 10 1 2.5 Q1 1 2.5 1 Z"/></svg>
        1300 287 419
      </div>
    </div>
    <div class="clinic">
      <div class="clinic-name">Riverbend Natural Therapies &amp; Herbal Practice</div>
      <div>19 Quillon Ave, Malvern East VIC 3145</div>
      <div class="clinic-phone">
        <svg viewBox="0 0 12 12" aria-hidden="true"><path d="M2.5 1 L4.5 1 L5 3.5 L3.8 4.4 Q5 7 7.6 8.2 L8.5 7 L11 7.5 L11 9.5 Q10.5 11 9 11 Q1 10 1 2.5 Q1 1 2.5 1 Z"/></svg>
        (03) 9731 4052
      </div>
    </div>
  </div>
</section>

</body>
</html>
```